Water ATM Card

Need a design for water ATM cards. Size of card is 3.375 x 2.125 inch
On the Front include the Cedar hollow Logo.
Bottom right corner should have Price $100
On the Back
This card is to be used to access water refills at any Cedar Hollow Water Vending Machines.
Please contact (869) 418 2930 or (869) 534 1276 or email clearflowbox@mailvista.example for any assistance or recharging of card.

```html
<!DOCTYPE html>
<html lang="en">
<head>
<meta charset="utf-8">
<title>Cedar Hollow Water Card</title>
<link rel="stylesheet" href="https://fonts.googleapis.com/css2?family=Montserrat:wght@400;500;700&display=swap">
<style>
  :root {
    --stage: #1c1c1c;
    --card-white: #ffffff;
    --brand-blue: #2a56a6;
    --ink: #1d1d1d;
    --price-green: #2f9e47;
    --back-top: #2f7fbe;
    --back-mid: #3b5799;
    --back-bottom: #2e3d8a;
    --on-blue: #ffffff;
  }
  * { margin: 0; padding: 0; box-sizing: border-box; }
  html, body {
    width: 1200px; height: 1059px; overflow: hidden;
    background: var(--stage);
    font-family: "Montserrat", sans-serif;
  }
  .card {
    position: absolute; left: 255px;
    width: 690px; height: 392px;
    border-radius: 26px;
  }
  .card-front { top: 89px; background: var(--card-white); }
  .card-back {
    top: 547px;
    background: linear-gradient(165deg, var(--back-top) 0%, var(--back-mid) 45%, var(--back-bottom) 100%);
    color: var(--on-blue);
  }
  .holder { position: absolute; left: 38px; top: 66px; }
  .holder-name {
    font-weight: 700; font-size: 22px; letter-spacing: 0.5px;
    color: var(--brand-blue); line-height: 1;
  }
  .holder-role {
    margin-top: 8px; font-size: 14px; font-weight: 400;
    color: var(--ink); letter-spacing: 0.5px;
  }
  .brand-front {
    position: absolute; right: 42px; top: 84px;
    font-weight: 700; font-size: 22px; color: var(--brand-blue);
    letter-spacing: 0.5px;
  }
  .contacts { position: absolute; left: 37px; top: 250px; list-style: none; }
  .contacts li {
    display: flex; align-items: center; gap: 8px;
    font-size: 15px; color: var(--ink); height: 23.5px;
  }
  .contacts li:first-child { margin-bottom: 5px; }
  .contacts svg { width: 14px; height: 14px; flex: none; fill: var(--brand-blue); }
  .price {
    position: absolute; left: 450px; top: 308px;
    font-weight: 700; font-size: 31px; color: var(--price-green);
  }
  .brand-back {
    position: absolute; left: 0; right: 0; top: 170px;
    text-align: center; font-weight: 700; font-size: 42px;
    letter-spacing: 1px; line-height: 1.2;
  }
  .back-note {
    position: absolute; left: 70px; right: 70px; bottom: 34px;
    text-align: center; font-size: 13.5px; font-weight: 500;
    line-height: 1.5;
  }
</style>
</head>
<body>
  <section class="card card-front">
    <div class="holder">
      <p class="holder-name">DANIEL REEVE</p>
      <p class="holder-role">OWER</p>
    </div>
    <p class="brand-front">CEDAR HOLLOW</p>
    <ul class="contacts">
      <li>
        <svg viewBox="0 0 24 24"><path d="M6.6 10.8a15 15 0 0 0 6.6 6.6l2.2-2.2c.3-.3.7-.4 1-.2 1.1.4 2.3.6 3.6.6.6 0 1 .4 1 1V20c0 .6-.4 1-1 1A17 17 0 0 1 3 4c0-.6.4-1 1-1h3.5c.6 0 1 .4 1 1 0 1.3.2 2.5.6 3.6.1.3 0 .7-.2 1z"/></svg>
        (869) 418 2930
      </li>
      <li>
        <svg viewBox="0 0 24 24"><path d="M7 1h10a2 2 0 0 1 2 2v18a2 2 0 0 1-2 2H7a2 2 0 0 1-2-2V3a2 2 0 0 1 2-2zm0 3v14h10V4zm5 15.5a1.2 1.2 0 1 0 0 2.4 1.2 1.2 0 0 0 0-2.4z"/></svg>
        (869) 534 1276
      </li>
      <li>
        <svg viewBox="0 0 24 24"><path d="M2 5h20v2l-10 6L2 7zm0 4.3l10 6 10-6V19H2z"/></svg>
        clearflowbox@mailvista.example
      </li>
      <li>
        <svg viewBox="0 0 24 24"><path d="M12 2a10 10 0 1 0 0 20 10 10 0 0 0 0-20zm-1 17.9A8 8 0 0 1 4 12l5 5v1a2 2 0 0 0 2 2zm6.9-2.5A2 2 0 0 0 16 16h-1v-3a1 1 0 0 0-1-1H8v-2h2a1 1 0 0 0 1-1V7h2a2 2 0 0 0 2-2v-.4a8 8 0 0 1 2.9 12.8z"/></svg>
        www.cedarhollowwater.example
      </li>
    </ul>
    <p class="price">Price $100</p>
  </section>

  <section class="card card-back">
    <p class="brand-back">CEDAR HOLLOW</p>
    <p class="back-note">This card is to be used to access water refills at any Cedar Hollow Water Vending Machines. Please contact (869) 418 2930 or (869) 534 1276 or email clearflowbox@mailvista.example for any assistance or recharging of card.</p>
  </section>
</body>
</html>
```